Telecommunications/Power civil contractor needs business card design

Were a new telecommunications/power underground civil contractor that is looking for a new business card design. Our company colours are silver or grey and orange. Feel free to use the white background logo or the black background logo.

Target Market(s)

Local contractors, utility companies, private sector mining/energy companies, developers.

Industry/Entity Type

Telecommunications

Contact Information for Business Card

Each card will need the following info:
Persons name:
Title:
E-mail:
Phone number:
Shop Address:
Mailing Address:

Requirements
Must have
• Each card will need the following info:
• Persons name:
• Title:
• E-mail:
• Phone number:
• Shop Address:
• Mailing Address:

```html
<!DOCTYPE html>
<html lang="en">
<head>
<meta charset="utf-8">
<title>Ridgeline Contracting Inc – Business Card</title>
<link rel="stylesheet" href="https://fonts.googleapis.com/css2?family=Open+Sans:wght@400;600;800&display=swap">
<style>
  :root{
    --stage:#2b2b2b;
    --card-white:#ffffff;
    --card-black:#050505;
    --orange:#f05a22;
    --grey:#6d6e71;
    --grey-light:#9a9b9e;
    --ink:#4a4a4a;
  }
  *{box-sizing:border-box;margin:0;padding:0}
  html,body{width:1200px;height:907px;overflow:hidden}
  body{
    background:var(--stage);
    font-family:"Open Sans",sans-serif;
    position:relative;
  }
  .card{
    position:absolute;
    top:305px;
    width:520px;
    height:297px;
    box-shadow:0 10px 30px rgba(0,0,0,.45);
    overflow:hidden;
  }
  .card--front{left:50px;background:var(--card-white)}
  .card--back{left:630px;background:var(--card-black)}

  .card__swoosh{position:absolute;inset:0;width:100%;height:100%}

  .brand{
    position:absolute;
    display:flex;
    align-items:center;
    gap:10px;
  }
  .brand__dot{
    width:34px;height:34px;border-radius:50%;
    border:3px solid var(--grey);
    flex:none;
  }
  .brand__name{
    font-weight:800;
    color:var(--orange);
    font-size:15px;
    line-height:1.1;
    letter-spacing:.5px;
    text-transform:uppercase;
  }
  .card--front .brand{left:30px;top:34px}
  .card--back .brand{right:30px;top:38px;flex-direction:row-reverse}
  .card--back .brand__dot{border-color:var(--grey-light)}

  .person{
    position:absolute;right:30px;top:30px;text-align:right;
  }
  .person__name{color:var(--orange);font-weight:600;font-size:13px}
  .person__title{color:var(--ink);font-size:12px}

  .address{
    position:absolute;right:30px;top:100px;text-align:right;
    color:var(--ink);font-size:11.5px;line-height:1.6;
  }

  .contact{
    position:absolute;left:30px;bottom:34px;
    list-style:none;color:var(--ink);font-size:12.5px;line-height:1.75;
  }
  .contact__item{display:flex;align-items:center;gap:8px}
  .contact__icon{width:12px;height:12px;fill:var(--orange);flex:none}
</style>
</head>
<body>

<section class="card card--front" aria-label="Business card front">
  <svg class="card__swoosh" viewBox="0 0 520 297" preserveAspectRatio="none" aria-hidden="true">
    <path d="M120,297 C280,262 420,205 520,130 L520,137 C420,215 290,272 150,297 Z" fill="var(--grey)"/>
    <path d="M150,297 C300,268 430,215 520,150 L520,188 C440,240 340,280 270,297 Z" fill="var(--orange)"/>
  </svg>

  <div class="brand">
    <span class="brand__dot"></span>
    <span class="brand__name">Ridgeline<br>Contracting Inc</span>
  </div>

  <div class="person">
    <p class="person__name">Dalton Reyes</p>
    <p class="person__title">Managing Director</p>
  </div>

  <address class="address">
    N. 7 Harbor Lane,<br>
    Suite 210, Millbrook, WA 55501
  </address>

  <ul class="contact">
    <li class="contact__item">
      <svg class="contact__icon" viewBox="0 0 24 24" aria-hidden="true"><path d="M6.6 10.8a15.1 15.1 0 0 0 6.6 6.6l2.2-2.2a1 1 0 0 1 1-.25 11.4 11.4 0 0 0 3.6.57 1 1 0 0 1 1 1V20a1 1 0 0 1-1 1A17 17 0 0 1 3 4a1 1 0 0 1 1-1h3.5a1 1 0 0 1 1 1c0 1.25.2 2.45.57 3.57a1 1 0 0 1-.25 1z"/></svg>
      555.014.722
    </li>
    <li class="contact__item">
      <svg class="contact__icon" viewBox="0 0 24 24" aria-hidden="true"><path d="M2 5h20v14H2z M2 5l10 8 10-8" stroke="#fff" stroke-width="1.5"/></svg>
      info@ridgelinecontracting.com
    </li>
  </ul>
</section>

<section class="card card--back" aria-label="Business card back">
  <div class="brand">
    <span class="brand__dot"></span>
    <span class="brand__name">Ridgeline<br>Contracting Inc</span>
  </div>
</section>

</body>
</html>
```